Redesign of business card for Cedar Ridge Mechanical

We are looking for a new design for our business cards for Cedar Ridge Mechanical. We are a plumbing & HVAC construction company, operating on the West Coast of Canada and USA. Logo attached.
Industry/Entity Type
Construction - Plumbing & HVAC
Contact Information for Business Card
Name, address, phone numbers, email, website address
Look and feel
Each slider illustrates characteristics of the customer's brand and the style your logo design should communicate.

```html
<!DOCTYPE html>
<html lang="en">
<head>
<meta charset="utf-8">
<title>Cedar Ridge Mechanical – Business Card</title>
<link href="https://fonts.googleapis.com/css2?family=Roboto:wght@400;700&family=Roboto+Condensed:wght@700&display=swap" rel="stylesheet">
<style>
  :root {
    --backdrop: #d6d6d6;
    --paper: #ffffff;
    --ink: #000000;
    --charcoal: #2f2f2f;
    --swoosh: #7a7a7a;
    --reverse: #ffffff;
  }
  * { margin: 0; padding: 0; box-sizing: border-box; }
  html, body { width: 1200px; height: 1040px; overflow: hidden; }
  body {
    background: var(--backdrop);
    font-family: "Roboto", Arial, sans-serif;
    position: relative;
  }
  .card {
    position: absolute;
    left: 285px;
    width: 643px;
    height: 366px;
    border-radius: 14px;
    overflow: hidden;
  }
  .card--front { top: 130px; background: var(--paper); }
  .card--back { top: 568px; background: var(--charcoal); }

  .card__wave { position: absolute; inset: 0; }

  .brand {
    position: absolute;
    display: flex;
    align-items: center;
    gap: 12px;
    font-weight: 700;
    text-transform: uppercase;
    letter-spacing: 0.5px;
  }
  .brand__mark { display: block; flex: none; }
  .brand--front {
    left: 54px; top: 78px;
    color: var(--ink);
    font-size: 22px;
    line-height: 1.15;
  }
  .brand--front .brand__mark { width: 22px; height: 22px; background: var(--ink); }
  .brand--back {
    left: 0; right: 0; top: 140px;
    justify-content: center;
    color: var(--reverse);
    font-size: 34px;
  }
  .brand--back .brand__mark { width: 30px; height: 30px; background: var(--reverse); }

  .contact {
    position: absolute;
    right: 35px;
    top: 122px;
    text-align: right;
    color: var(--reverse);
  }
  .contact__name {
    font-family: "Roboto Condensed", "Arial Narrow", sans-serif;
    font-weight: 700;
    font-size: 25px;
    line-height: 1.1;
  }
  .contact__title { font-size: 16px; margin-top: 2px; }
  .contact__address { font-size: 15.5px; line-height: 20px; margin-top: 38px; }
  .contact__lines { list-style: none; margin-top: 20px; font-size: 15.5px; line-height: 20px; }
  .contact__lines li { display: flex; justify-content: flex-end; align-items: center; gap: 10px; }
  .contact__icon { width: 13px; height: 13px; flex: none; }

  .back__web {
    position: absolute;
    left: 0; right: 0; top: 323px;
    text-align: center;
    color: var(--reverse);
    font-size: 16px;
  }
</style>
</head>
<body>
  <section class="card card--front" aria-label="Business card front">
    <svg class="card__wave" viewBox="0 0 643 366" width="643" height="366" aria-hidden="true">
      <path d="M0 236 C150 300 320 300 430 170 S575 38 643 50 L643 366 L0 366 Z" fill="var(--swoosh)"/>
      <path d="M0 264 C170 320 340 300 440 180 S580 58 643 76 L643 366 L0 366 Z" fill="var(--ink)"/>
    </svg>

    <div class="brand brand--front">
      <span class="brand__mark"></span>
      <span>Cedar Ridge<br>Mechanical</span>
    </div>

    <div class="contact">
      <div class="contact__name">Marcus Hale</div>
      <div class="contact__title">President</div>
      <div class="contact__address">2170 Harbor View Road<br>Coast Ridge, WA 98201</div>
      <ul class="contact__lines">
        <li>(604) 5120-7781
          <svg class="contact__icon" viewBox="0 0 16 16" aria-hidden="true"><path fill="#fff" d="M3.6 1l2.3 3-1.3 1.6c.9 2 2.6 3.7 4.6 4.6l1.6-1.3 3 2.3-1.5 2.5C6.8 13.4 2.6 9.2 1.3 2.6z"/></svg>
        </li>
        <li>name@cedarridgemechanical.com
          <svg class="contact__icon" viewBox="0 0 16 16" aria-hidden="true"><rect x="1" y="3" width="14" height="10" fill="#fff"/><path d="M1 3l7 6 7-6" fill="none" stroke="#000" stroke-width="1.3"/></svg>
        </li>
        <li>www.cedarridgemechanical.com
          <svg class="contact__icon" viewBox="0 0 16 16" aria-hidden="true"><circle cx="8" cy="8" r="7" fill="#fff"/><path d="M5 4c2 1 1 3 3 3s1 3 3 3M4 11c1-1 2 0 3 1" fill="none" stroke="#000" stroke-width="1.3"/></svg>
        </li>
      </ul>
    </div>
  </section>

  <section class="card card--back" aria-label="Business card back">
    <div class="brand brand--back">
      <span class="brand__mark"></span>
      <span>Cedar Ridge Mechanical</span>
    </div>
    <div class="back__web">www.cedarridgemechanical.com</div>
  </section>
</body>
</html>
```